Business Cards Needed for Innovative Healthcare Marketing Company

We are a marketing company focused on healthcare. Our company is all about rebranding yourself renewing your image and generating results. The phoenix stands for "reborn" or "rising" which we provide new brands for our clients we take their old brands and renew it with creativity and innovation. I am looking for a business card with color dimension. I have attached an example of a card I think has the look and feel of what I am trying to accomplish. I like that the card example has black and grey font colors, I like the font placement and the small logo, I really like the use of the colors on the right those are the colors of my logo. My logo is phoenix so maybe incorporating flames similar to that design. I would like the back a solid color maybe red with an opaque version of the logo and website. As a marketing company I am always open to creative liberty!

Target Market(s)

Doctors and business professionals.

Industry/Entity Type

Marketing

Contact Information for Business Card

Valcorne Health Care Marketing
Marla Tenwick- CEO
#(512)638-2974
email-marla@valcorne.com
website- valcorne.com

Font styles to use
Sans Serif

Colors
ec1f27
f37122
ffc214
fbed22
fbf289
f04a50

Requirements
Must have
• The logo and required information
Nice to have
• icons by the information
Should not have
• child like font

```html
<!DOCTYPE html>
<html lang="en">
<head>
<meta charset="utf-8">
<title>Valcorne Health Care Marketing – Business Card</title>
<link rel="stylesheet" href="https://fonts.googleapis.com/css2?family=Arimo:wght@400;700&display=swap">
<style>
  :root {
    --stage: #5a4430;
    --card-black: #0d0d0d;
    --card-black-soft: #1c1c1c;
    --orange-light: #f7b04a;
    --orange: #f39a26;
    --orange-deep: #e2721c;
    --white: #ffffff;
    --ink: #141414;
    --brand-red: #d9434a;
    --brand-orange: #f37122;
  }
  * { margin: 0; padding: 0; box-sizing: border-box; }
  html, body { width: 1200px; height: 858px; overflow: hidden; }
  body {
    background: var(--stage);
    font-family: "Arimo", Arial, sans-serif;
    position: relative;
  }
  .card {
    position: absolute;
    width: 540px;
    height: 310px;
    overflow: hidden;
    box-shadow: 0 14px 30px rgba(0,0,0,0.45);
  }
  .card-front { left: 50px; top: 150px; }
  .card-back {
    left: 610px; top: 398px;
    background: radial-gradient(ellipse at 30% 20%, var(--card-black-soft), var(--card-black) 70%);
  }
  .card-art { position: absolute; inset: 0; }

  .holder { position: absolute; right: 24px; top: 22px; text-align: right; }
  .holder-name { color: var(--white); font-weight: 700; font-size: 30px; letter-spacing: -0.3px; }
  .holder-role { color: var(--orange); font-weight: 700; font-size: 17px; margin-top: 2px; }

  .contacts {
    position: absolute; right: 22px; top: 130px;
    list-style: none; text-align: right;
  }
  .contacts li {
    display: flex; align-items: center; justify-content: flex-end;
    gap: 12px; color: var(--ink); font-size: 20px; line-height: 1; margin-bottom: 20px;
    white-space: nowrap;
  }
  .contacts svg { width: 16px; height: 16px; flex: none; }

  .brand {
    position: absolute; text-align: center; color: var(--brand-red);
    font-weight: 400; letter-spacing: 3px;
  }
  .brand-front { left: 8px; top: 168px; width: 210px; }
  .brand-back { left: 0; right: 0; top: 118px; }
  .brand-name { display: flex; align-items: center; justify-content: center; gap: 8px; white-space: nowrap; }
  .brand-front .brand-name { font-size: 25px; letter-spacing: 2px; }
  .brand-back .brand-name { font-size: 40px; }
  .brand-mark {
    width: 12px; height: 12px; border-radius: 50%; background: var(--brand-orange); flex: none;
  }
  .brand-back .brand-mark { width: 18px; height: 18px; }
  .brand-tagline {
    margin-top: 6px; padding-top: 6px; border-top: 1px solid var(--brand-red);
    font-size: 10px; letter-spacing: 1.5px; display: inline-block; white-space: nowrap;
  }
  .brand-back .brand-tagline { font-size: 14px; letter-spacing: 2px; }
</style>
</head>
<body>

  <section class="card card-front" aria-label="Business card front">
    <svg class="card-art" viewBox="0 0 540 310" preserveAspectRatio="none" aria-hidden="true">
      <defs>
        <linearGradient id="panelGlow" x1="0" y1="0" x2="1" y2="0">
          <stop offset="0" stop-color="#f7b04a"/>
          <stop offset="0.55" stop-color="#f39a26"/>
          <stop offset="1" stop-color="#e2721c"/>
        </linearGradient>
        <linearGradient id="blackSheen" x1="0" y1="0" x2="1" y2="1">
          <stop offset="0" stop-color="#262626"/>
          <stop offset="1" stop-color="#080808"/>
        </linearGradient>
      </defs>
      <rect class="front-base" width="540" height="310" fill="url(#blackSheen)"/>
      <polygon class="contact-panel" points="217,95 540,95 540,310 289,310" fill="url(#panelGlow)"/>
      <polygon class="logo-field" points="0,102 213,102 281,310 0,310" fill="#111"/>
      <polyline class="chevron-rule" points="0,100 215,100 285,310" fill="none" stroke="#ffffff" stroke-width="5"/>
      <line class="chevron-accent" x1="0" y1="93" x2="217" y2="93" stroke="#f39a26" stroke-width="4"/>
    </svg>

    <div class="holder">
      <p class="holder-name">Marla Tenwick</p>
      <p class="holder-role">CEO</p>
    </div>

    <ul class="contacts">
      <li>valcorne.com
        <svg viewBox="0 0 16 16" aria-hidden="true"><rect width="16" height="16" rx="2" fill="#141414"/><circle cx="8" cy="8" r="4.5" fill="none" stroke="#f39a26" stroke-width="1.3"/><line x1="3.5" y1="8" x2="12.5" y2="8" stroke="#f39a26" stroke-width="1.1"/></svg>
      </li>
      <li>#(512)638-2974
        <svg viewBox="0 0 16 16" aria-hidden="true"><rect width="16" height="16" rx="2" fill="#141414"/><path d="M5 4h2l1 2.5-1.2.8a6 6 0 0 0 2 2l.8-1.2L12 9v2a1 1 0 0 1-1 1A7 7 0 0 1 4 5a1 1 0 0 1 1-1z" fill="#f39a26"/></svg>
      </li>
      <li>marla@valcorne.com
        <svg viewBox="0 0 16 16" aria-hidden="true"><rect width="16" height="16" rx="2" fill="#141414"/><rect x="3.5" y="5" width="9" height="6.5" fill="none" stroke="#f39a26" stroke-width="1.2"/><polyline points="3.5,5 8,9 12.5,5" fill="none" stroke="#f39a26" stroke-width="1.2"/></svg>
      </li>
    </ul>

    <div class="brand brand-front">
      <p class="brand-name"><span class="brand-mark" aria-hidden="true"></span>VALCORNE</p>
      <p class="brand-tagline">HEALTH CARE MARKETING</p>
    </div>
  </section>

  <section class="card card-back" aria-label="Business card back">
    <div class="brand brand-back">
      <p class="brand-name"><span class="brand-mark" aria-hidden="true"></span>VALCORNE</p>
      <p class="brand-tagline">HEALTH CARE MARKETING</p>
    </div>
  </section>

</body>
</html>
```